KPL Construction we build lodges in Botswana

We need a Design Layout only with Categories where we can update each projects photos.... We have a web address and a host - kpl.construction

```html
<!DOCTYPE html>
<html lang="en">
<head>
<meta charset="utf-8">
<title>KPL Construction</title>
<link rel="stylesheet" href="https://fonts.googleapis.com/css2?family=Raleway:wght@200;400;600&family=Montserrat:wght@400;600&family=Audiowide&family=Arimo:wght@700&family=Tinos&family=Great+Vibes&display=swap">
<style>
:root{
  --blue:#1a6fd0;
  --blue-deep:#1f3f9a;
  --red:#e2232b;
  --red-soft:#d9464c;
  --ink:#222;
  --muted:#777;
  --white:#fff;
  --metal-1:#9a9ca0;
  --metal-2:#d6d8db;
  --teal:#3aa9a0;
  --tile-shade:rgba(20,14,10,.22);
}
*{margin:0;padding:0;box-sizing:border-box}
html,body{width:1200px;height:3072px;overflow:hidden}
body{position:relative;background:#1b1b1b;font-family:"Montserrat",sans-serif;color:var(--ink)}
.abs{position:absolute}

/* header */
.site-header{position:absolute;left:0;top:0;width:1200px;height:100px;background:rgba(255,255,255,.88);z-index:3}
.brand{position:absolute;left:22px;top:30px;display:flex;align-items:center;gap:10px;font-weight:600;font-size:20px;color:var(--blue)}
.brand-mark{width:28px;height:28px;background:var(--red)}
.main-nav{position:absolute;left:608px;top:27px;display:flex;align-items:center;height:49px;font-size:10px;font-weight:600;letter-spacing:.5px}
.main-nav a{color:#333;text-decoration:none;margin-right:40px}
.main-nav a.active{background:var(--blue);color:#fff;padding:0 12px;height:49px;line-height:49px;margin-right:26px;font-size:8px}
.cart{position:absolute;left:1070px;top:31px;display:flex;align-items:center;gap:8px;font-size:10px;font-weight:600}
.cart-icon{width:38px;height:38px;border:3px solid #333;border-radius:50%;display:flex;align-items:center;justify-content:center}

/* hero */
.hero{position:absolute;left:0;top:0;width:1200px;height:545px;overflow:hidden}
.hero-photo{position:absolute;left:0;top:0;width:1200px;height:545px;background:
  radial-gradient(ellipse 260px 420px at 240px 420px,rgba(40,40,40,.55),transparent 70%),
  radial-gradient(ellipse 260px 420px at 900px 400px,rgba(40,40,40,.5),transparent 70%),
  linear-gradient(180deg,#b9b9b9 0%,#8a8a8a 35%,#6a6a6a 70%,#9d9d9d 92%,#c9c9c9 100%)}
.hero-title{position:absolute;left:0;width:1200px;text-align:center;font-family:"Raleway",sans-serif;font-weight:200}
.hero-title.line1{top:158px;font-size:68px;letter-spacing:10px;color:rgba(255,255,255,.85)}
.hero-title.line2{top:232px;font-size:66px;letter-spacing:16px;color:rgba(40,40,40,.5)}
.hero-sub{position:absolute;left:435px;top:316px;width:330px;text-align:center;font-size:12px;line-height:19px;color:rgba(255,255,255,.85);font-family:"Raleway",sans-serif}
.btn-start{position:absolute;left:475px;top:393px;width:258px;height:53px;border-radius:8px;background:linear-gradient(180deg,#4aa0ff,#1650d8 60%,#0c2fa0);border:3px solid #9cc8ff;color:#fff;font-family:"Audiowide",sans-serif;font-size:24px;text-align:center;line-height:47px;letter-spacing:2px}

/* gallery */
.gallery{position:absolute;left:0;top:545px;width:1200px;height:1330px;background:linear-gradient(135deg,var(--metal-1) 0%,var(--metal-2) 35%,#a8aaae 60%,#e2e3e5 85%,var(--metal-1) 100%)}
.section-title{position:absolute;left:0;top:62px;width:1200px;text-align:center;font-family:"Audiowide",sans-serif;font-size:44px;letter-spacing:3px}
.t-blue{color:var(--blue-deep)}
.t-red{color:var(--red)}
.arrow{position:absolute;top:298px}
.slide{position:absolute}
.slide-side{top:213px;width:260px;height:198px;border:2px solid #333;box-shadow:0 3px 8px rgba(0,0,0,.35)}
.slide-main{left:385px;top:153px;width:434px;height:316px;background:#3a3a3a;border:2px solid #222;box-shadow:0 4px 12px rgba(0,0,0,.4)}
.slide-main .photo{position:absolute;left:50px;top:40px;width:334px;height:236px}
.slide-close{position:absolute;left:400px;top:40px;width:18px;height:18px;background:#ddd;border:1px solid #555}
.slide-caption{position:absolute;left:0;top:480px;width:1200px;text-align:center;font-size:17px;font-weight:600;letter-spacing:2px;color:#fff}
.slide-date{position:absolute;left:0;top:507px;width:1200px;text-align:center;font-family:"Great Vibes",cursive;font-size:30px;color:#fff}
.grid{position:absolute;left:41px;top:553px;width:1112px;height:731px;display:grid;grid-template-columns:repeat(3,1fr);grid-template-rows:repeat(3,1fr);gap:4px;background:#333;border:2px solid #333}
.tile{position:relative;box-shadow:inset 0 0 0 2000px var(--tile-shade)}
.spinner{position:absolute;left:50%;top:50%;width:48px;height:48px;margin:-24px 0 0 -24px;background:#000;border-radius:4px}
.dots{position:absolute;left:0;top:1300px;width:1200px;display:flex;justify-content:center;gap:8px}
.dots span{width:9px;height:9px;border-radius:50%;background:#f2f2f2;border:1px solid #aaa}
.dots span.on{background:var(--blue)}

/* articles */
.articles-band{position:absolute;left:0;top:1874px;width:1200px;height:113px;background:var(--red-soft);border-top:6px solid var(--blue-deep);border-bottom:6px solid var(--blue-deep);text-align:center;font-family:"Arimo",sans-serif;font-weight:700;font-size:40px;color:#fff;line-height:100px}
.article{position:absolute;top:1990px;width:394px;height:294px;color:#fff}
.article p{position:absolute;left:32px;top:32px;width:290px;font-family:"Tinos",serif;font-size:20px;line-height:27px}
.article time{position:absolute;left:32px;top:133px;font-size:11px}

/* subscribe */
.subscribe{position:absolute;left:0;top:2284px;width:1200px;height:624px;background:linear-gradient(180deg,#595959 0%,#8a8a8a 25%,#4a4a4a 55%,#1e1e1e 80%,#151515 100%)}
.subscribe-text{position:absolute;left:0;top:148px;width:1200px;text-align:center;color:#fff;font-size:20px}
.email-field{position:absolute;left:338px;top:208px;width:403px;height:41px;background:#fff;font-size:9px;letter-spacing:2px;color:#999;padding-left:22px;line-height:41px}
.btn-sub{position:absolute;left:741px;top:208px;width:123px;height:41px;background:var(--blue);color:#fff;font-family:"Audiowide",sans-serif;font-size:11px;text-align:center;line-height:41px}
.info-card{position:absolute;top:421px;width:252px;height:144px;background:#fff;border-bottom:3px solid var(--teal);text-align:center}
.info-card svg{margin-top:30px}
.info-card h4{font-size:9px;letter-spacing:2px;font-weight:400;margin-top:6px}
.info-card p{font-size:9px;color:var(--muted);margin-top:42px}

/* footer */
.site-footer{position:absolute;left:0;top:2908px;width:1200px;height:164px;background:linear-gradient(180deg,var(--red) 0%,var(--red) 25%,#9a3a7a 55%,#3f5fcf 100%)}
.footer-brand{position:absolute;left:24px;top:90px;display:flex;align-items:center;gap:12px;font-weight:600;font-size:26px;color:var(--blue-deep)}
.footer-brand .brand-mark{width:34px;height:34px}
.social{position:absolute;left:348px;top:13px;display:flex;gap:25px}
.social span{position:relative;width:41px;height:41px;border-radius:50%;background:radial-gradient(circle at 40% 35%,#e8313a,#b8121a 70%);border:2px solid #7a0a10;box-shadow:0 2px 4px rgba(0,0,0,.35)}
.social span::after{content:"";position:absolute;left:11px;top:11px;width:15px;height:15px;border-radius:50%;border:2px solid rgba(120,10,16,.8)}
</style>
</head>
<body>

<section class="hero">
  <div class="hero-photo" role="img" aria-label="Black and white photo of baobab trees in open bushland"></div>
  <h1 class="hero-title line1">KPL</h1>
  <div class="hero-title line2">CONSTRUCTION</div>
  <p class="hero-sub">We are a construction company based in the Okavango Delta and specialize in Lodge building</p>
  <div class="btn-start">GET STARTED</div>
</section>

<header class="site-header">
  <div class="brand"><span class="brand-mark"></span>KPL Construction</div>
  <nav class="main-nav">
    <a class="active">HOME</a><a>GALLERY</a><a>TOP</a><a>BLOG</a><a>CONTAKT</a>
  </nav>
  <div class="cart">CART
    <span class="cart-icon"><svg width="16" height="16" viewBox="0 0 16 16"><path d="M2 4h12l-1.5 8h-9z" fill="var(--red)"/></svg></span>
  </div>
</header>

<section class="gallery">
  <h2 class="section-title"><span class="t-blue">OUR</span> <span class="t-red">GALLERY</span></h2>
  <svg class="arrow" style="left:12px" width="20" height="30" viewBox="0 0 20 30"><path d="M16 3 4 15l12 12" fill="none" stroke="#333" stroke-width="5"/></svg>
  <svg class="arrow" style="left:1166px" width="20" height="30" viewBox="0 0 20 30"><path d="M4 3l12 12L4 27" fill="none" stroke="#333" stroke-width="5"/></svg>

  <div class="slide slide-side" style="left:88px;background:radial-gradient(ellipse at 50% 35%,#d98a4a 0%,#a5521f 55%,#5e2a0c 100%)" role="img" aria-label="Project cover with city typography artwork"></div>
  <div class="slide slide-side" style="left:846px;background:linear-gradient(160deg,#eef4ef 0%,#bcd6cb 45%,#6f9a8b 100%)" role="img" aria-label="Project cover with Valencia typography artwork"></div>
  <div class="slide slide-main">
    <div class="photo" role="img" aria-label="Bright open-plan lodge interior with kitchen and lounge" style="background:linear-gradient(180deg,#efe9e1 0%,#ddd3c6 45%,#b8a692 62%,#8f7c68 100%)"></div>
    <svg class="slide-close" viewBox="0 0 18 18"><path d="M4 4l10 10M14 4 4 14" stroke="#444" stroke-width="2"/></svg>
  </div>
  <div class="slide-caption">CITIES &amp; TYPOGRAPHY</div>
  <div class="slide-date">Jun 26th</div>

  <div class="grid">
    <div class="tile" role="img" aria-label="Dining area with blue chairs" style="background:linear-gradient(180deg,#e6e0d8 0%,#cfc4b6 55%,#a08e7a 72%,#7d6c5a 100%)"></div>
    <div class="tile" role="img" aria-label="Dining room with pendant lamps" style="background:linear-gradient(180deg,#ece8e2 0%,#d9d1c8 55%,#b5a797 72%,#8c7e70 100%)"></div>
    <div class="tile" role="img" aria-label="Bedroom with wooden floor" style="background:linear-gradient(180deg,#a9a49e 0%,#8a837b 50%,#9e8468 72%,#6a5640 100%)"></div>
    <div class="tile" role="img" aria-label="Living room with grey sofa" style="background:linear-gradient(180deg,#ece7e0 0%,#dcd3c8 55%,#b79f86 75%,#98806a 100%)"></div>
    <div class="tile" role="img" aria-label="Lounge with wood panelled wall" style="background:linear-gradient(90deg,#5a3f2c 0%,#7a5a42 40%,#8a8580 65%,#cfcac4 100%)">
      <svg class="spinner" viewBox="0 0 48 48"><g stroke="#fff" stroke-width="3" stroke-linecap="round"><path d="M24 8v7" opacity="1"/><path d="M35.3 12.7l-5 5" opacity=".85"/><path d="M40 24h-7" opacity=".7"/><path d="M35.3 35.3l-5-5" opacity=".55"/><path d="M24 40v-7" opacity=".4"/><path d="M12.7 35.3l5-5" opacity=".3"/><path d="M8 24h7" opacity=".2"/><path d="M12.7 12.7l5 5" opacity=".12"/></g></svg>
    </div>
    <div class="tile" role="img" aria-label="Reading corner with wooden chair" style="background:linear-gradient(180deg,#c7bcae 0%,#9a8876 50%,#6f5a46 75%,#4c3c2e 100%)"></div>
    <div class="tile" role="img" aria-label="Bright bedroom with striped bedding" style="background:linear-gradient(180deg,#f0ece6 0%,#e2dbd2 50%,#d6a866 68%,#b7824a 85%,#c7b7a6 100%)"></div>
    <div class="tile" role="img" aria-label="Sitting room with armchair and floor lamp" style="background:linear-gradient(180deg,#eceae6 0%,#d8d4ce 55%,#b7aea4 75%,#8a7e72 100%)"></div>
    <div class="tile" role="img" aria-label="Hallway leading to bedroom" style="background:linear-gradient(90deg,#4a4440 0%,#6a625c 30%,#d6d2cc 55%,#e6e2dc 100%)"></div>
  </div>
  <div class="dots"><span class="on"></span><span></span><span></span><span></span><span></span><span></span><span></span><span></span></div>
</section>

<div class="articles-band">Our Latest Articles</div>

<article class="article" style="left:0;background:linear-gradient(180deg,#3a3230,#6a5a50)" role="img" aria-label="Person with coffee cup at a laptop">
  <p>Etiam commodo convallis quis minim veniam, quis nostrud exercitation veniam.</p><time>May 27, 2015</time>
</article>
<article class="article" style="left:401px;background:linear-gradient(180deg,#6f7f90,#4c5d70)" role="img" aria-label="Traveller looking over the horizon">
  <p>Lorem ipsum dolor sit amet conse ctetur adipisicing elit, labore et dolore aliqua.</p><time>May 17, 2015</time>
</article>
<article class="article" style="left:806px;background:linear-gradient(180deg,#5e5a58,#3e3a38)" role="img" aria-label="Knitted scarf and coat">
  <p>Etiam commodo convallis quis minim veniam, quis nostrud exercitation veniam.</p><time>May 27, 2015</time>
</article>

<section class="subscribe" role="img" aria-label="Misty forest landscape">
  <svg class="abs" style="left:586px;top:118px" width="26" height="24" viewBox="0 0 26 24"><path d="M2 11 24 2l-6 20-6-8z" fill="none" stroke="#fff" stroke-width="2"/></svg>
  <p class="subscribe-text">Subscribe to receive updates!</p>
  <div class="email-field">ENTER EMAIL ADDRESS...</div>
  <div class="btn-sub">SUBSCRIBE</div>

  <div class="info-card" style="left:203px">
    <svg width="14" height="16" viewBox="0 0 14 16"><path d="M7 1a5 5 0 0 1 5 5c0 4-5 9-5 9S2 10 2 6a5 5 0 0 1 5-5z" fill="var(--teal)"/></svg>
    <h4>ADDRESS</h4><p>27 Mokolodi Road, Gaborone</p>
  </div>
  <div class="info-card" style="left:475px">
    <svg width="16" height="12" viewBox="0 0 16 12"><rect x="1" y="1" width="14" height="10" fill="none" stroke="var(--teal)" stroke-width="2"/><path d="M1 1l7 6 7-6" fill="none" stroke="var(--teal)" stroke-width="2"/></svg>
    <h4>EMAIL</h4><p>hello@kpl.construction</p>
  </div>
  <div class="info-card" style="left:745px">
    <svg width="10" height="16" viewBox="0 0 10 16"><rect x="1" y="1" width="8" height="14" rx="1.5" fill="none" stroke="var(--teal)" stroke-width="2"/></svg>
    <h4>PHONE</h4><p>+267 390 1184</p>
  </div>
</section>

<footer class="site-footer">
  <div class="social" aria-label="Social links"><span></span><span></span><span></span><span></span><span></span><span></span><span></span><span></span></div>
  <div class="footer-brand"><span class="brand-mark"></span>KPL Construction</div>
</footer>

</body>
</html>
```